Pre-Paid Card for Teens needs a design

We are a Fintech company called Toqavel. We will sell prepaid cards for families and teens. Now we need a prepaid card design. Prepaid card should have a orbitpay logo, company logo, 16 card number, expire date. Our webpage is http://www.toqavel-example.com
Target Market(s)
Teenages between 8 - 18 years old
Industry/Entity Type
It Company
Requirements
Must have
- The prepaid card must include toqavel logo, orbitpay debit card logo (I already attached a sample card), 16 digit card number and expire date.
Nice to have
- It should be fun and prestigious for young people.
Should not have
- We don't want that the card has a lots of color

```html
<!DOCTYPE html>
<html lang="en">
<head>
<meta charset="utf-8">
<title>Toqavel Prepaid Card</title>
<link rel="stylesheet" href="https://fonts.googleapis.com/css2?family=Fredoka:wght@600&family=Roboto:wght@500;700&family=Share+Tech+Mono&display=swap">
<style>
  :root {
    --backdrop: #5b2412;
    --card-black: #050505;
    --brand-yellow: #fbbf1d;
    --brand-orange: #ee7b24;
    --brand-purple: #6a3597;
    --deep-purple: #230b47;
    --ink-white: #ffffff;
    --seal-silver: #c9ced3;
  }
  html, body {
    margin: 0;
    width: 1200px;
    height: 1200px;
    overflow: hidden;
    background: var(--backdrop);
  }
  .stage {
    position: relative;
    width: 1200px;
    height: 1200px;
  }
  .prepaid-card {
    position: absolute;
    left: 217px;
    top: 359px;
    width: 766px;
    height: 482px;
    filter: drop-shadow(0 4px 6px rgba(0,0,0,0.35));
  }
  .brand-name {
    font-family: "Fredoka", sans-serif;
    font-weight: 600;
    font-size: 54px;
    fill: var(--brand-yellow);
  }
  .card-number {
    font-family: "Share Tech Mono", monospace;
    font-size: 44px;
    fill: var(--ink-white);
    letter-spacing: 6px;
  }
  .bin-label {
    font-family: "Roboto", sans-serif;
    font-weight: 700;
    font-size: 18px;
    fill: var(--ink-white);
  }
  .valid-label {
    font-family: "Roboto", sans-serif;
    font-weight: 500;
    font-size: 15px;
    fill: var(--ink-white);
  }
  .expiry-date {
    font-family: "Share Tech Mono", monospace;
    font-size: 34px;
    fill: var(--ink-white);
    letter-spacing: 4px;
  }
  .network-name {
    font-family: "Fredoka", sans-serif;
    font-weight: 600;
    font-size: 30px;
    fill: var(--ink-white);
  }
  .icon-badge { fill: var(--brand-orange); }
  .icon-line { fill: none; stroke: var(--ink-white); stroke-width: 3; stroke-linejoin: round; stroke-linecap: round; }
  .icon-fill { fill: var(--ink-white); }
</style>
</head>
<body>
<main class="stage">
  <svg class="prepaid-card" viewBox="280 402 958 602" xmlns="http://www.w3.org/2000/svg" role="group" aria-label="Toqavel prepaid debit card">
    <defs>
      <clipPath id="card-shape">
        <rect x="280" y="402" width="958" height="602" rx="22"/>
      </clipPath>
      <radialGradient id="seal-sheen" cx="45%" cy="40%" r="65%">
        <stop offset="0" stop-color="#f3f5f7"/>
        <stop offset="1" stop-color="#8d959c"/>
      </radialGradient>
    </defs>

    <g clip-path="url(#card-shape)">
      <rect class="card-base" x="280" y="402" width="958" height="602" fill="var(--card-black)"/>
      <circle class="corner-sun" cx="1140" cy="438" r="98" fill="var(--brand-orange)"/>
      <circle class="corner-moon" cx="330" cy="940" r="62" fill="var(--deep-purple)"/>

      <g class="center-blobs">
        <ellipse cx="760" cy="740" rx="300" ry="175" transform="rotate(-32 760 740)" fill="var(--brand-purple)"/>
        <ellipse cx="752" cy="742" rx="270" ry="125" transform="rotate(-18 752 742)" fill="var(--deep-purple)"/>
      </g>

      <g class="confetti-dots">
        <circle cx="612" cy="562" r="17" fill="var(--deep-purple)"/>
        <circle cx="1019" cy="566" r="21" fill="var(--brand-purple)"/>
        <circle cx="1064" cy="656" r="20" fill="var(--deep-purple)"/>
        <circle cx="777" cy="938" r="10" fill="var(--brand-yellow)"/>
      </g>
    </g>

    <g class="brand-lockup">
      <circle cx="372" cy="486" r="30" fill="var(--brand-purple)"/>
      <text class="brand-name" x="448" y="503">toqavel</text>
    </g>

    <g class="icon phone-icon">
      <circle class="icon-badge" cx="872" cy="462" r="39"/>
      <rect class="icon-line" x="862" y="444" width="20" height="35" rx="3"/>
      <circle class="icon-fill" cx="872" cy="473" r="2"/>
    </g>
    <g class="icon mail-icon">
      <circle class="icon-badge" cx="451" cy="651" r="39"/>
      <rect class="icon-line" x="433" y="640" width="36" height="26" rx="2"/>
      <path class="icon-line" d="M433 642 L451 656 L469 642"/>
    </g>
    <g class="icon savings-icon" role="img" aria-label="Piggy bank savings icon">
      <circle class="icon-badge" cx="1168" cy="620" r="39"/>
    </g>
    <g class="icon wallet-icon">
      <circle class="icon-badge" cx="472" cy="896" r="39"/>
      <rect class="icon-line" x="453" y="884" width="38" height="28" rx="4"/>
      <rect class="icon-fill" x="478" y="893" width="14" height="10" rx="2"/>
    </g>

    <text class="card-number" x="348" y="773">5157 5500 0000 0000</text>
    <text class="bin-label" x="350" y="818">5157</text>
    <text class="valid-label" x="756" y="818">VALID</text>
    <text class="valid-label" x="756" y="836">THRU</text>
    <text class="expiry-date" x="842" y="837">10/20</text>

    <g class="network-badge">
      <rect x="1030" y="731" width="172" height="225" rx="40" fill="none" stroke="var(--ink-white)" stroke-width="2.5"/>
      <ellipse class="security-seal" cx="1116" cy="795" rx="72" ry="48" fill="url(#seal-sheen)"/>
      <text class="network-name" x="1116" y="910" text-anchor="middle">orbitpay</text>
    </g>
  </svg>
</main>
</body>
</html>
```